Brantor Works Business Card

Modern and Professional Business Card for a Med size construction/development company.

See the samples below for the design I like … but I need ideas for incorporating the red company logo while still keeping the clean look of the card samples that are attached.

Logo and tag line on the back … info on the front.

Tagline: Solid Work from the Footing Up

Target Market(s)

Med-Large General Contractors

Contact Information for Business Card

Brantor Works Limited
42 Fenwick Avenue
Mt. Pearl, NL
A1N 4R9

t: 709-555-0147
f: 709-555-0182
w: www.brantorworks-example.com

Font styles to use
Sans Serif

Colors
fbee3e

Requirements
Must have
• I like the black and yellow designs of the attached samples …. but I'm not sure how to incorporate the red Brantor Works logo into that design??
Nice to have
• Construction safety strips

```html
<!DOCTYPE html>
<html lang="en">
<head>
<meta charset="utf-8">
<title>Brantor Works Business Card</title>
<link href="https://fonts.googleapis.com/css2?family=Archivo:wght@800&family=Lato:wght@400;700&display=swap" rel="stylesheet">
<style>
  :root {
    --stage: #333335;
    --card-red: #e41f26;
    --card-black: #262626;
    --ink-dark: #1c1c1c;
    --paper-white: #ffffff;
  }
  * { box-sizing: border-box; margin: 0; padding: 0; }
  html, body {
    width: 1200px; height: 866px; overflow: hidden;
    background: var(--stage);
  }
  .canvas { position: relative; width: 1200px; height: 866px; }

  .card {
    position: absolute; top: 283px;
    width: 520px; height: 300px; overflow: hidden;
    box-shadow: 0 6px 18px rgba(0,0,0,.45);
  }

  /* Front: contact details */
  .card--front { left: 50px; background: var(--card-black); font-family: "Lato", sans-serif; color: var(--paper-white); }
  .band { position: absolute; background: var(--card-red); display: flex; flex-direction: column; justify-content: center; }
  .band--name {
    top: 42px; left: 0; width: 290px; height: 46px; padding-left: 26px;
    clip-path: polygon(0 0, 100% 0, 95% 100%, 0 100%);
  }
  .band--title {
    top: 94px; left: 0; width: 272px; height: 36px; padding-left: 26px;
    clip-path: polygon(0 0, 100% 0, 95% 100%, 0 100%);
  }
  .person-name { font-family: "Archivo", sans-serif; font-weight: 800; font-size: 20px; letter-spacing: .5px; color: var(--ink-dark); text-transform: uppercase; white-space: nowrap; }
  .person-role { font-size: 14px; color: var(--ink-dark); white-space: nowrap; }

  .band--contact { right: 0; padding-left: 34px; clip-path: polygon(18px 0, 100% 0, 100% 100%, 0 100%); }
  .band--phones { top: 112px; left: 290px; height: 62px; }
  .band--web { top: 180px; left: 250px; height: 36px; }
  .band--address { top: 222px; left: 236px; height: 52px; }
  .contact-line { display: flex; align-items: center; gap: 8px; font-size: 13.5px; line-height: 1.35; white-space: nowrap; }
  .contact-line svg { width: 15px; height: 15px; flex: none; fill: var(--ink-dark); }
  .address-text { line-height: 1.3; }

  /* Back: name and tagline */
  .card--back { left: 630px; background: var(--card-red); display: flex; flex-direction: column; align-items: center; justify-content: center; gap: 22px; }
  .company-name {
    font-family: "Archivo", sans-serif; font-weight: 800; font-size: 34px;
    color: var(--ink-dark); text-transform: uppercase; text-align: center; line-height: 1.1;
  }
  .tagline { font-family: "Lato", sans-serif; font-weight: 700; font-size: 14px; letter-spacing: 1px; color: var(--paper-white); text-transform: uppercase; white-space: nowrap; }
</style>
</head>
<body>
<main class="canvas">

  <section class="card card--front" aria-label="Card front">
    <div class="band band--name"><span class="person-name">Daniel Morrow</span></div>
    <div class="band band--title"><span class="person-role">Managing Director</span></div>

    <div class="band band--contact band--phones">
      <p class="contact-line">
        <svg viewBox="0 0 24 24" aria-hidden="true"><path d="M6.6 10.8a15 15 0 0 0 6.6 6.6l2.2-2.2c.3-.3.7-.4 1-.2 1.1.4 2.3.6 3.6.6.6 0 1 .4 1 1V20c0 .6-.4 1-1 1A17 17 0 0 1 3 4c0-.6.4-1 1-1h3.5c.6 0 1 .4 1 1 0 1.3.2 2.5.6 3.6.1.3 0 .7-.2 1z"/></svg>
        709-555-0147
      </p>
      <p class="contact-line">
        <svg viewBox="0 0 24 24" aria-hidden="true"><path d="M6 2h12v5H6zM4 8h16a2 2 0 0 1 2 2v7h-4v5H6v-5H2v-7a2 2 0 0 1 2-2zm4 8v4h8v-4z"/></svg>
        709-555-0182
      </p>
    </div>
    <div class="band band--contact band--web">
      <p class="contact-line">
        <svg viewBox="0 0 24 24" aria-hidden="true"><path d="M12 2a10 10 0 1 0 0 20 10 10 0 0 0 0-20zm6.9 6h-3a15 15 0 0 0-1.3-3.9A8 8 0 0 1 18.9 8zM12 4c.8 1.2 1.5 2.5 1.9 4h-3.8c.4-1.5 1.1-2.8 1.9-4zM4.3 14a8 8 0 0 1 0-4h3.4a16 16 0 0 0 0 4zm.8 2h3a15 15 0 0 0 1.3 3.9A8 8 0 0 1 5.1 16zm3-8h-3a8 8 0 0 1 4.3-3.9C8.8 5.3 8.4 6.6 8.1 8zM12 20c-.8-1.2-1.5-2.5-1.9-4h3.8c-.4 1.5-1.1 2.8-1.9 4zm2.3-6H9.7a14 14 0 0 1 0-4h4.6a14 14 0 0 1 0 4zm.3 5.9c.6-1.2 1-2.5 1.3-3.9h3a8 8 0 0 1-4.3 3.9zm1.7-5.9a16 16 0 0 0 0-4h3.4a8 8 0 0 1 0 4z"/></svg>
        www.brantorworks-example.com
      </p>
    </div>
    <div class="band band--contact band--address">
      <p class="contact-line">
        <svg viewBox="0 0 24 24" aria-hidden="true"><path d="M12 2a7 7 0 0 0-7 7c0 5.2 7 13 7 13s7-7.8 7-13a7 7 0 0 0-7-7zm0 9.5A2.5 2.5 0 1 1 12 6.5a2.5 2.5 0 0 1 0 5z"/></svg>
        <span class="address-text">42 Fenwick Avenue<br>Harbour Vale, NL A0B 2C3</span>
      </p>
    </div>
  </section>

  <section class="card card--back" aria-label="Card back">
    <h1 class="company-name">Brantor Works<br>Limited</h1>
    <p class="tagline">Solid Work from the Footing Up</p>
  </section>

</main>
</body>
</html>
```